Website for Dental Office - The Bright Arch Clinic

The bright arch clinic is a dental office offering cosmetic dentistry, general dentistry, and multi-specialty dental care all under one roof in our state-of-the-art cosmetic dental center. We are particularly striving to provide services that fit the need of the young generation. Thus, we hope to have a modern, professional concise website that represents our spirit.

*Should be able to switch from English to Chinese

6 sections besides homepage:
Home, Meet us, Services,
Patient Info, Cases&Reviews, Blog, Contact

The Services sections should contain multiple subsections such as cleaning and prevention, cosmetic dentistry, implant dentistry, removable dentures, etc...
The Patient Info section is also intended to contain several subsections such as
New Patient offer, accepted Insurance, patient portal, helpful tips, etc...

Target Market(s)

young generation

Coding

Coded - Design and coding required

Number of Pages Required

5+ page

Font styles to use
Sans Serif

Colors
0592cd
33a6d7
85cae6
00a990
33b8a4
86cfc6
cee9f5
cfeae6
3277b5

Requirements
Must have
• *Should be able to switch from English to Chinese
Nice to have
• http://www.thebrightarchclinic.com/
• As a reference, the above link is the current website, but we would like to change the appearance and the content (our new logo's picture is attached)

```html
<!DOCTYPE html>
<html lang="en">
<head>
<meta charset="utf-8">
<title>The Bright Arch Clinic</title>
<link href="https://fonts.googleapis.com/css2?family=Poppins:ital,wght@0,400;0,500;0,600;0,700;1,400&display=swap" rel="stylesheet">
<style>
:root{
  --green:#00a990;
  --green-dark:#009a83;
  --blue:#33a6d7;
  --blue-deep:#0592cd;
  --blue-soft:#85cae6;
  --ink:#1f1f1f;
  --text:#555;
  --muted:#777;
  --band:#f1f1f1;
  --footer:#262626;
  --white:#fff;
}
*{box-sizing:border-box;margin:0;padding:0}
html,body{width:1200px;height:3597px;overflow:hidden}
body{font-family:'Poppins',sans-serif;color:var(--ink);background:var(--white);position:relative}
section,header,footer{position:absolute;left:0;width:1200px}
.abs{position:absolute}
.btn{position:absolute;display:flex;align-items:center;justify-content:center;gap:8px;background:var(--green);color:var(--white);border-radius:30px;font-weight:600;text-transform:uppercase;white-space:nowrap}
.btn .dot{width:14px;height:14px;border-radius:50%;background:var(--white);display:flex;align-items:center;justify-content:center}
.btn .dot svg{width:8px;height:8px}
.section-title{position:absolute;left:0;width:1200px;text-align:center;font-size:40px;font-weight:500;letter-spacing:-.5px}

/* header */
.site-header{top:0;height:105px;background:var(--white)}
.brand{left:110px;top:30px;display:flex;align-items:center;gap:12px}
.brand-mark{width:42px;height:42px;background:var(--blue);border-radius:4px}
.brand-name{font-size:21px;font-weight:600;color:var(--blue);line-height:21px;width:140px}
.contact-item{display:flex;align-items:center;gap:11px;top:14px}
.icon-circle{width:36px;height:36px;border-radius:50%;background:var(--blue);display:flex;align-items:center;justify-content:center}
.icon-circle svg{width:18px;height:18px}
.contact-item .lines{font-size:14px;line-height:21px;color:#333}
.contact-item .small{font-size:11px;line-height:14px;color:#333}
.contact-item .phone{font-size:18px;font-weight:600;color:#222;line-height:24px}
.main-nav{top:74px;left:373px;display:flex;gap:24px;font-size:15px;font-weight:500;color:#222}
.main-nav a{color:inherit;text-decoration:none;position:relative;padding:0 5px 9px}
.main-nav a.active{color:var(--blue)}
.main-nav a.active::after{content:"";position:absolute;left:0;right:0;bottom:0;height:3px;background:var(--blue)}
.lang{display:flex;align-items:center;gap:5px}
.lang .flag{width:11px;height:11px;border-radius:50%;background:#d33;display:inline-block}

/* hero */
.hero{top:105px;height:511px}
.hero-photo{position:absolute;inset:0;background:linear-gradient(100deg,#c9d3e6 0%,#dde4f0 35%,#b7c7e6 60%,#8aa6da 100%)}
.hero h1{position:absolute;left:110px;top:150px;font-size:50px;line-height:58px;font-weight:700;color:var(--ink);letter-spacing:-1.5px}
.hero .btn{left:110px;top:300px;width:196px;height:53px;font-size:17px}

/* about */
.about{top:616px;height:497px}
.about h2{position:absolute;left:600px;top:88px;font-size:40px;font-weight:500;letter-spacing:-.5px}
.about p{position:absolute;left:600px;top:158px;width:488px;font-size:14.5px;line-height:27.5px;color:var(--text);text-align:justify}
.about .btn{left:600px;top:359px;width:153px;height:38px;font-size:13px}

/* services */
.services{top:1113px;height:629px;background:var(--band)}
.services .section-title{top:68px}
.service-card{position:absolute;top:133px;width:318px;height:437px;background:var(--white);border:1px solid #e2e2e2}
.service-photo{height:206px}
.service-icon{position:absolute;left:131px;top:178px;width:56px;height:56px;border-radius:50%;background:var(--blue);border:3px solid var(--white);display:flex;align-items:center;justify-content:center}
.service-icon svg{width:28px;height:28px}
.service-card h3{position:absolute;left:17px;top:242px;font-size:16px;font-weight:600;text-transform:uppercase;color:#222;white-space:nowrap}
.service-card p{position:absolute;left:17px;top:281px;width:286px;font-size:13.5px;line-height:27.5px;color:var(--text);text-align:justify}
.service-card .btn{left:17px;top:380px;width:141px;height:37px;font-size:13px}
.slider-arrow{position:absolute;width:38px;height:38px;border-radius:50%;border:1.5px solid #333;display:flex;align-items:center;justify-content:center}
.slider-arrow svg{width:12px;height:12px}

/* team */
.team{top:1742px;height:574px}
.team .section-title{top:90px}
.team-card{position:absolute;top:174px;width:245px;height:300px;background:var(--white);border:1px solid #e6e6e6}
.team-card.featured{box-shadow:0 4px 14px rgba(0,0,0,.2);border-color:#ddd}
.team-photo{height:209px}
.team-card h4{position:absolute;left:22px;top:227px;font-size:16px;font-weight:600;white-space:nowrap}
.team-card span{position:absolute;left:22px;top:258px;font-size:13px;color:var(--muted);white-space:nowrap}
.team-card.featured h4,.team-card.featured span{left:9px}
.team-card.wide h4,.team-card.wide span{left:34px}
.team-card .btn{left:58px;top:160px;width:129px;height:33px;font-size:13px}

/* testimonials */
.testimonials{top:2316px;height:387px;background:linear-gradient(90deg,#4f9ff0,#5aa6ee 50%,#4c9bec)}
.testimonials .section-title{top:54px;color:var(--white);font-weight:600}
.quote{position:absolute;left:285px;top:136px;width:630px;text-align:center;font-style:italic;font-size:14.5px;line-height:29px;color:var(--white)}
.qmark{position:absolute;font-size:34px;font-weight:700;color:var(--white);font-family:Georgia,serif;line-height:34px}
.stars{position:absolute;left:0;width:1200px;top:272px;text-align:center;color:#ffd21a;font-size:17px;letter-spacing:2px}
.client{position:absolute;left:0;width:1200px;top:300px;text-align:center;color:var(--white);font-size:14px;font-weight:500;text-transform:uppercase}
.testimonials .slider-arrow{border-color:var(--white)}

/* patient info */
.patient{top:2703px;height:542px}
.patient h2{position:absolute;left:110px;top:96px;font-size:40px;font-weight:500;letter-spacing:-.5px}
.patient p{position:absolute;left:112px;width:520px;font-size:14.5px;line-height:28px;color:#333}
.patient a{color:var(--blue);text-decoration:none}
.patient-photo{position:absolute;left:747px;top:117px;width:341px;height:263px;background:linear-gradient(135deg,#dfe9f5,#a9c7e6 55%,#7ea9d8);box-shadow:0 2px 8px rgba(0,0,0,.15)}
.patient .btn{left:112px;top:404px;width:151px;height:42px;font-size:13px}

/* footer */
.site-footer{top:3245px;height:352px;background:var(--footer);color:#ddd}
.footer-brand{left:110px;top:66px;display:flex;align-items:center;gap:10px}
.footer-brand .brand-mark{width:34px;height:34px}
.footer-brand .brand-name{font-size:15px;line-height:17px;width:150px}
.footer-about{left:111px;top:180px;width:222px;font-size:13.5px;line-height:25px;color:#ddd}
.footer-col h5{font-size:17px;font-weight:600;color:var(--white);margin-bottom:22px}
.footer-col li{list-style:none;font-size:14px;line-height:32.5px;color:#ddd;white-space:nowrap}
.footer-col li::before{content:"» ";color:#ddd}
.contact-list li::before{content:none}
.contact-list li{display:flex;gap:14px;align-items:flex-start;line-height:24px;margin-bottom:10px}
.contact-list svg{width:13px;height:13px;margin-top:5px;flex:none}
.footer-bottom{left:0;top:300px;width:1200px;height:1px;background:#3a3a3a}
.copyright{left:111px;top:320px;font-size:14px;color:#ddd}
.socials{left:943px;top:311px;display:flex;gap:7px}
.socials span{width:31px;height:31px;border-radius:50%;border:1px solid #ccc}
</style>
</head>
<body>

<header class="site-header">
  <div class="abs brand"><span class="brand-mark"></span><span class="brand-name">THE BRIGHT ARCH CLINIC</span></div>
  <div class="abs contact-item" style="left:485px">
    <span class="icon-circle"><svg viewBox="0 0 24 24" fill="none" stroke="#fff" stroke-width="2"><path d="M12 22s7-7 7-12a7 7 0 0 0-14 0c0 5 7 12 7 12z"/><circle cx="12" cy="10" r="2.5"/></svg></span>
    <div class="lines">275 Harbor Lane<br>Suite 210</div>
  </div>
  <div class="abs contact-item" style="left:717px">
    <span class="icon-circle"><svg viewBox="0 0 24 24" fill="#fff"><path d="M6.6 10.8a15 15 0 0 0 6.6 6.6l2.2-2.2a1 1 0 0 1 1-.25 11 11 0 0 0 3.6.6 1 1 0 0 1 1 1V20a1 1 0 0 1-1 1A17 17 0 0 1 3 4a1 1 0 0 1 1-1h3.5a1 1 0 0 1 1 1 11 11 0 0 0 .6 3.6 1 1 0 0 1-.25 1z"/></svg></span>
    <div><div class="small">Call Us Today</div><div class="phone">555 014 2290</div></div>
  </div>
  <div class="btn" style="left:918px;top:11px;width:170px;height:41px;font-size:13px">Get Appointment</div>
  <nav class="abs main-nav">
    <a class="active">Home</a><a>Meet us</a><a>Services</a><a>Patient Info</a><a>Cases&amp;Reviews</a><a>Blog</a><a>Contact</a>
    <a class="lang"><span class="flag"></span>Eng <svg width="9" height="6" viewBox="0 0 9 6"><path d="M0 0h9L4.5 6z" fill="#222"/></svg></a>
  </nav>
</header>

<section class="hero">
  <div class="hero-photo" role="img" aria-label="Smiling patient in a dental chair while a gloved dentist examines her teeth"></div>
  <h1>YOUR SMILE OUR<br>PASSION</h1>
  <div class="btn">Learn More <span class="dot"><svg viewBox="0 0 8 8"><path d="M2 1l3 3-3 3" stroke="#00a990" stroke-width="1.6" fill="none"/></svg></span></div>
</section>

<section class="about">
  <svg class="abs" style="left:111px;top:132px" width="393" height="244" role="img" aria-label="Dentist treating a patient in a bright modern treatment room">
    <defs><linearGradient id="ag" x1="0" y1="0" x2="1" y2="1"><stop offset="0" stop-color="#9fb3c4"/><stop offset=".5" stop-color="#d8e2ea"/><stop offset="1" stop-color="#8ea4b6"/></linearGradient></defs>
    <path d="M0 0H393V244C300 205 90 205 0 244Z" fill="url(#ag)"/>
  </svg>
  <h2>ABOUT US</h2>
  <p>Welcome to The Bright Arch Clinic where we specialize in General and Cosmetic Dentistry, Dental Implants, Periodontics (Gum Surgery), Endodontics (Root Canal Treatment) and Reconstructive Dentistry for patients in Boston, Brookline, Cambridge, Brighton, Allston, Newton, Watertown, Wellesley and all other surrounding neighborhoods of Boston, Massachusetts.</p>
  <div class="btn">Learn More <span class="dot"><svg viewBox="0 0 8 8"><path d="M2 1l3 3-3 3" stroke="#00a990" stroke-width="1.6" fill="none"/></svg></span></div>
</section>

<section class="services">
  <h2 class="section-title">OUR SERVICES</h2>
  <div class="slider-arrow" style="left:33px;top:332px"><svg viewBox="0 0 12 12"><path d="M8 1L3 6l5 5" stroke="#333" stroke-width="1.6" fill="none"/></svg></div>
  <div class="slider-arrow" style="left:1127px;top:332px"><svg viewBox="0 0 12 12"><path d="M4 1l5 5-5 5" stroke="#333" stroke-width="1.6" fill="none"/></svg></div>

  <article class="service-card" style="left:111px">
    <div class="service-photo" role="img" aria-label="Dentist performing a professional cleaning" style="background:linear-gradient(135deg,#e8e2dc,#c9d6df 60%,#aac3d4)"></div>
    <span class="service-icon"><svg viewBox="0 0 24 24" fill="#fff"><path d="M7 3c-2.5 0-4 2-4 4.5 0 3 1.5 4.5 2 7.5.5 3 1 6 2.5 6s1.8-4 2.5-6c.3-1 .7-1.5 2-1.5s1.7.5 2 1.5c.7 2 1 6 2.5 6s2-3 2.5-6c.5-3 2-4.5 2-7.5C21 5 19.5 3 17 3c-2 0-3 1-5 1S9 3 7 3z"/></svg></span>
    <h3>Cleaning and Prevention</h3>
    <p>Professional dental cleanings (oral prophylaxis) are usually performed by the dentist</p>
    <div class="btn">Read More <span class="dot"><svg viewBox="0 0 8 8"><path d="M2 1l3 3-3 3" stroke="#00a990" stroke-width="1.6" fill="none"/></svg></span></div>
  </article>

  <article class="service-card" style="left:441px">
    <div class="service-photo" role="img" aria-label="Patient comparing a porcelain veneer shade guide" style="background:linear-gradient(135deg,#cfc2b5,#e2d9cf 55%,#b9c9d6)"></div>
    <span class="service-icon"><svg viewBox="0 0 24 24" fill="#fff"><path d="M7 3c-2.5 0-4 2-4 4.5 0 3 1.5 4.5 2 7.5.5 3 1 6 2.5 6s1.8-4 2.5-6c.3-1 .7-1.5 2-1.5s1.7.5 2 1.5c.7 2 1 6 2.5 6s2-3 2.5-6c.5-3 2-4.5 2-7.5C21 5 19.5 3 17 3c-2 0-3 1-5 1S9 3 7 3z"/></svg></span>
    <h3>Cosmetic Dentistry</h3>
    <p>Veneers are very thin pieces of durable, tooth shaped porcelain that are custom made and bonded</p>
    <div class="btn">Read More <span class="dot"><svg viewBox="0 0 8 8"><path d="M2 1l3 3-3 3" stroke="#00a990" stroke-width="1.6" fill="none"/></svg></span></div>
  </article>

  <article class="service-card" style="left:771px">
    <div class="service-photo" role="img" aria-label="Dentist using an instrument on a smiling patient" style="background:linear-gradient(135deg,#9fb0bf,#d9dfe4 55%,#8d9fb0)"></div>
    <span class="service-icon"><svg viewBox="0 0 24 24" fill="#fff"><path d="M6 3h12c1.5 0 2 1 2 2.5S18 10 12 10 4 7 4 5.5 4.5 3 6 3z"/><rect x="9" y="11" width="6" height="2" rx="1"/><rect x="9.5" y="14" width="5" height="2" rx="1"/><rect x="10" y="17" width="4" height="2" rx="1"/><path d="M11 20h2l-1 2z"/></svg></span>
    <h3>Implant Dentistry</h3>
    <p>Dental implants are a great way to replace missing teeth and also provide a fixed solution to having removable</p>
    <div class="btn">Read More <span class="dot"><svg viewBox="0 0 8 8"><path d="M2 1l3 3-3 3" stroke="#00a990" stroke-width="1.6" fill="none"/></svg></span></div>
  </article>
</section>

<section class="team">
  <h2 class="section-title">MEET OUR TEAM</h2>
  <article class="team-card" style="left:137px">
    <div class="team-photo" role="img" aria-label="Portrait of the orthodontist" style="background:linear-gradient(135deg,#8a6a45,#c7a57a 60%,#6b4e32)"></div>
    <h4>Lena Farrow, Dmd, Ms</h4><span>Board Certified Orthodontist</span>
  </article>
  <article class="team-card featured" style="left:456px">
    <div class="team-photo" role="img" aria-label="Portrait of the pediatric dentist" style="background:linear-gradient(135deg,#bfa495,#d8c3b4 55%,#4a4a4a)"></div>
    <div class="btn">More Info <span class="dot"><svg viewBox="0 0 8 8"><path d="M2 1l3 3-3 3" stroke="#00a990" stroke-width="1.6" fill="none"/></svg></span></div>
    <h4>Harold B. Whitcomb, Dmd</h4><span>Board Certified Pediatric Dentist</span>
  </article>
  <article class="team-card wide" style="left:775px">
    <div class="team-photo" role="img" aria-label="Portrait of the general dentist" style="background:linear-gradient(135deg,#d8dde0,#e9e6e2 55%,#b9a08a)"></div>
    <h4>Dr. Nadia Serrano, Dmd</h4><span>General Dentist</span>
  </article>
</section>

<section class="testimonials">
  <h2 class="section-title">WHAT OUR CLIENTS SAY</h2>
  <div class="slider-arrow" style="left:111px;top:176px"><svg viewBox="0 0 12 12"><path d="M8 1L3 6l5 5" stroke="#fff" stroke-width="1.6" fill="none"/></svg></div>
  <div class="slider-arrow" style="left:1050px;top:176px"><svg viewBox="0 0 12 12"><path d="M4 1l5 5-5 5" stroke="#fff" stroke-width="1.6" fill="none"/></svg></div>
  <span class="qmark" style="left:253px;top:128px">“</span>
  <p class="quote">I LOVE everyone at this office!! Dr. Farrow is the best of the best. The office staff are always courteous and kind, even kept an eye on my granddaughter who was watching TV while I was being seen. They are professional, nice, outgoing, friendly--just what every office strives to be--they have it all!!</p>
  <span class="qmark" style="left:795px;top:246px">”</span>
  <div class="stars">★★★★★</div>
  <div class="client">Maren Holt</div>
</section>

<section class="patient">
  <h2>PATIENT INFO</h2>
  <p style="top:160px">Thank you for your trust in us. We look forward to working with you towards a healthy and beautiful smile.</p>
  <p style="top:218px">Prior to your first appointment, we request that you please download and complete: The New Patient Form – Adults or <a>The New Patient Form</a> – <a>Children (16 &amp; Under)</a>.</p>
  <p style="top:304px">We accept most insurance and all major credit cards. We also offer special finance option through Smile Credit Plan.</p>
  <div class="patient-photo" role="img" aria-label="Dental assistant reviewing a tablet with a smiling patient"></div>
  <div class="btn">Learn More <span class="dot"><svg viewBox="0 0 8 8"><path d="M2 1l3 3-3 3" stroke="#00a990" stroke-width="1.6" fill="none"/></svg></span></div>
</section>

<footer class="site-footer">
  <div class="abs footer-brand"><span class="brand-mark"></span><span class="brand-name">THE BRIGHT ARCH CLINIC</span></div>
  <p class="abs footer-about">Our specialist are also trained in providing Botox and Dermal Fillers and we would be honored to have you a part</p>
  <div class="abs footer-col" style="left:399px;top:73px">
    <h5>Useful Links</h5>
    <ul><li>Meet us</li><li>Services</li><li>Patient Info</li><li>Cases&amp;Reviews</li><li>Blog</li></ul>
  </div>
  <div class="abs footer-col" style="left:600px;top:73px">
    <h5>Treatments</h5>
    <ul><li>Cleaning &amp; prevention</li><li>Cosmetic dentistry</li><li>Implant dentistry</li><li>Removable dentures</li></ul>
  </div>
  <div class="abs footer-col" style="left:855px;top:73px">
    <h5>Contact us</h5>
    <ul class="contact-list">
      <li><svg viewBox="0 0 24 24" fill="#ddd"><path d="M12 22s7-7 7-12a7 7 0 0 0-14 0c0 5 7 12 7 12zm0-9a3 3 0 1 1 0-6 3 3 0 0 1 0 6z"/></svg><span>275 Harbor Lane, Suite<br>210, Brookline MA 02400</span></li>
      <li><svg viewBox="0 0 24 24" fill="#ddd"><path d="M6.6 10.8a15 15 0 0 0 6.6 6.6l2.2-2.2a1 1 0 0 1 1-.25 11 11 0 0 0 3.6.6 1 1 0 0 1 1 1V20a1 1 0 0 1-1 1A17 17 0 0 1 3 4a1 1 0 0 1 1-1h3.5a1 1 0 0 1 1 1 11 11 0 0 0 .6 3.6 1 1 0 0 1-.25 1z"/></svg><span>1-555-014-7731</span></li>
      <li><svg viewBox="0 0 24 24" fill="none" stroke="#ddd" stroke-width="2"><rect x="3" y="5" width="18" height="14" rx="1"/><path d="M3 6l9 7 9-7"/></svg><span>hello@brightarchclinic.example</span></li>
    </ul>
  </div>
  <div class="abs footer-bottom"></div>
  <div class="abs copyright">© 2019 The Bright Arch Clinic. All Rights Reserved</div>
  <div class="abs socials"><span></span><span></span><span></span><span></span></div>
</footer>

</body>
</html>
```